Young, dynamic furniture company needs a new business card design

We require a new business card design for our modern furniture company which supplies furniture and appliances to the property and development market.
Oakridge Interiors has become one of the leading furniture & appliance suppliers to the property market withing London. With over 10 years experience, we have increased our business to supply not only private landlords and managing agents, but also property developers, housing associations and local councils.
We offer not only a complete range of furniture which includes beds, wardrobes, dining sets and sofas, but also a high quality, full delivery and assembly service to help you with all our furnishing needs.

Target Market(s)

Private landlords, estate agents, letting agents, property management companies

Industry/Entity Type

Business

Contact Information for Business Card

Name,
Title,
Address,
Mobile,
Telephone,
Fax, Website, email address

Font styles to use
Sans Serif

Colors
3176b5
0555a3
85abd2
cfdeed

Requirements
Must have
• All the above information for each of our staff, along with our logo

```html
<!DOCTYPE html>
<html lang="en">
<head>
<meta charset="utf-8">
<title>Oakridge Interiors – Business Card</title>
<link href="https://fonts.googleapis.com/css2?family=Open+Sans:wght@300;400;700&display=swap" rel="stylesheet">
<style>
  :root {
    --brand-blue: #1a6fb5;
    --brand-navy: #1f3a73;
    --ink: #1e1e20;
    --paper: #ffffff;
    --backdrop: #d2d1cf;
    --rule: #2a2a2a;
  }
  * { margin: 0; padding: 0; box-sizing: border-box; }
  html, body {
    width: 1200px; height: 994px; overflow: hidden;
    background: var(--backdrop);
    font-family: "Open Sans", Arial, sans-serif;
    color: var(--ink);
  }
  .card {
    position: absolute;
    width: 760px; height: 434px;
    background: var(--paper);
    box-shadow: 0 10px 28px rgba(0,0,0,0.22);
    overflow: hidden;
  }
  .card--front { left: 80px; top: 50px; }
  .card--back { left: 360px; top: 510px; }
  .card__band { position: absolute; inset: 0; width: 100%; height: 100%; }
  .card__band polygon { fill: var(--brand-blue); }

  .brand { position: absolute; display: flex; align-items: flex-start; gap: 14px; }
  .brand__square {
    width: 64px; height: 64px; flex: none;
    background: var(--brand-navy);
    border: 4px solid var(--paper);
  }
  .brand__text { padding-top: 14px; }
  .brand__name {
    font-weight: 300; font-size: 30px; letter-spacing: 0.5px;
    text-transform: uppercase; line-height: 1; white-space: nowrap;
    color: var(--ink);
  }
  .brand__tagline {
    font-weight: 300; font-size: 15px; letter-spacing: 0.3px;
    text-transform: uppercase; margin-top: 6px; white-space: nowrap;
  }
  .card--front .brand { left: 232px; top: 196px; }
  .card--back .brand { right: 44px; top: 104px; }

  .rule { position: absolute; height: 1px; background: var(--rule); }
  .card--front .rule { left: 40px; right: 40px; top: 404px; }
  .front__web { position: absolute; right: 44px; top: 378px; font-size: 15px; }

  .holder { position: absolute; left: 40px; top: 62px; color: var(--paper); }
  .holder__name { font-weight: 700; font-size: 30px; text-transform: uppercase; line-height: 1.1; }
  .holder__role { font-size: 15px; text-transform: uppercase; letter-spacing: 0.5px; }

  .contacts { position: absolute; left: 56px; top: 284px; list-style: none; }
  .contacts li { display: flex; align-items: center; gap: 10px; font-size: 16px; line-height: 24px; }
  .contacts svg { width: 16px; height: 16px; fill: var(--brand-navy); flex: none; }

  .address { position: absolute; right: 40px; top: 300px; font-size: 16px; white-space: nowrap; }
  .card--back .rule--address { left: 360px; right: 40px; top: 330px; }
  .card--back .rule--base { left: 40px; width: 360px; top: 404px; }
</style>
</head>
<body>

<section class="card card--front" aria-label="Business card front">
  <svg class="card__band" viewBox="0 0 760 434" preserveAspectRatio="none" aria-hidden="true">
    <polygon points="0,0 760,0 760,130 0,250"/>
  </svg>
  <div class="brand">
    <span class="brand__square"></span>
    <div class="brand__text">
      <p class="brand__name">Oakridge Interiors</p>
      <p class="brand__tagline">Trade Furniture Solutions</p>
    </div>
  </div>
  <p class="front__web">www.website.com</p>
  <div class="rule"></div>
</section>

<section class="card card--back" aria-label="Business card back">
  <svg class="card__band" viewBox="0 0 760 434" preserveAspectRatio="none" aria-hidden="true">
    <polygon points="0,0 760,0 760,96 0,160"/>
  </svg>
  <div class="holder">
    <p class="holder__name">Your Name</p>
    <p class="holder__role">Position</p>
  </div>
  <div class="brand">
    <span class="brand__square"></span>
    <div class="brand__text">
      <p class="brand__name">Oakridge Interiors</p>
      <p class="brand__tagline">Trade Furniture Solutions</p>
    </div>
  </div>

  <ul class="contacts">
    <li><svg viewBox="0 0 16 16" aria-hidden="true"><path d="M3 1h3l1.5 3.5-2 1.3a9 9 0 0 0 4.7 4.7l1.3-2L15 10v3a2 2 0 0 1-2 2A12 12 0 0 1 1 3a2 2 0 0 1 2-2z"/></svg>123-456-7890</li>
    <li><svg viewBox="0 0 16 16" aria-hidden="true"><path d="M4 1h8v4H4zM1 6h14v6h-3v3H4v-3H1zM5 10v4h6v-4z"/></svg>123-456-7890</li>
    <li><svg viewBox="0 0 16 16" aria-hidden="true"><path d="M1 3h14v10H1zM2.5 4.5 8 9l5.5-4.5v-.2H2.5z"/></svg>youremail@oakridgemail.com</li>
    <li><svg viewBox="0 0 16 16" aria-hidden="true"><path fill-rule="evenodd" d="M8 1a7 7 0 1 1 0 14A7 7 0 0 1 8 1zm-.7 1.6A5.5 5.5 0 0 0 5 7.3h2.3zm1.4 0v4.7H11a5.5 5.5 0 0 0-2.3-4.7zM2.6 7.3h1.6A7 7 0 0 1 5.6 3a5.5 5.5 0 0 0-3 4.3zm10.8 0A5.5 5.5 0 0 0 10.4 3a7 7 0 0 1 1.4 4.3zM2.6 8.7a5.5 5.5 0 0 0 3 4.3 7 7 0 0 1-1.4-4.3zm2.4 0a5.5 5.5 0 0 0 2.3 4.7V8.7zm3.7 0v4.7A5.5 5.5 0 0 0 11 8.7zm3.1 0a7 7 0 0 1-1.4 4.3 5.5 5.5 0 0 0 3-4.3z"/></svg>www.website.com</li>
  </ul>

  <p class="address">PO BOX 1234, Address Line 1, Address Line 2,</p>
  <div class="rule rule--address"></div>
  <div class="rule rule--base"></div>
</section>

</body>
</html>
```